New letter head for Air Conditioning business

We need a new professional letter head design to suit our new re-branded air conditioning business. Our new logo is attached

```html
<!DOCTYPE html>
<html lang="en">
<head>
<meta charset="utf-8">
<title>Nordvent Letterhead</title>
<link href="https://fonts.googleapis.com/css2?family=Open+Sans:wght@400;600;700&family=Lato:wght@400;700&display=swap" rel="stylesheet">
<style>
  :root{
    --green:#66c088;
    --red:#ee6b5f;
    --charcoal:#3f3f41;
    --ink:#4a4a4a;
    --paper:#ffffff;
    --sign:#c9c9cc;
  }
  *{margin:0;padding:0;box-sizing:border-box}
  html,body{width:1040px;height:1200px;overflow:hidden;background:var(--paper)}
  .letterhead{position:relative;width:1040px;height:1200px;background:var(--paper);font-family:"Open Sans",sans-serif;color:var(--ink)}

  .header-band{position:absolute;left:0;top:0;width:1040px;height:52px;background:var(--green)}
  .header-rule{position:absolute;left:0;top:58px;width:1040px;height:5px;background:var(--red)}

  .footer-rule-red{position:absolute;left:0;top:1036px;width:1040px;height:5px;background:var(--red)}
  .footer-rule-green{position:absolute;left:0;top:1046px;width:1040px;height:7px;background:var(--green)}
  .footer-band{position:absolute;left:0;top:1060px;width:1040px;height:140px;background:var(--charcoal)}

  .brand{position:absolute;left:600px;top:84px;display:flex;flex-direction:column;align-items:flex-start}
  .brand-row{display:flex;align-items:center;gap:14px}
  .brand-dot{width:34px;height:34px;border-radius:50%;background:var(--green)}
  .brand-name{font-weight:700;font-size:40px;letter-spacing:4px;color:var(--charcoal);line-height:1}
  .brand-tagline{margin-top:8px;margin-left:90px;font-size:10.5px;font-weight:700;letter-spacing:2.1px;color:var(--green)}

  .issue-date{position:absolute;left:98px;top:216px;font-size:15px}
  .recipient{position:absolute;left:98px;top:253px;font-size:15px;line-height:18px}
  .salutation{position:absolute;left:98px;top:356px;font-size:15px}
  .paragraph{position:absolute;left:98px;width:840px;font-size:16px;line-height:27px;text-align:justify}
  .p1{top:407px}.p2{top:568px}.p3{top:676px}

  .closing{position:absolute;left:98px;top:815px;font-size:15px}
  .signature-mark{position:absolute;left:98px;top:854px;width:240px;height:22px;background:var(--sign);border-radius:11px;opacity:.55}
  .signer-name{position:absolute;left:98px;top:890px;font-size:19px;font-weight:600;color:#333}
  .signer-title{position:absolute;left:98px;top:922px;font-size:15px}

  .contact{position:absolute;right:100px;top:1074px;font-family:"Lato",sans-serif;color:#fff;font-size:18px;line-height:19.5px;text-align:right}
  .contact-line{display:flex;justify-content:flex-end;align-items:center;gap:8px}
  .contact-line svg{width:15px;height:15px}
  .contact-address{position:absolute;right:89px;top:1145px;font-family:"Lato",sans-serif;color:#fff;font-size:19px}
</style>
</head>
<body>
<main class="letterhead">
  <div class="header-band"></div>
  <div class="header-rule"></div>

  <div class="brand">
    <div class="brand-row">
      <span class="brand-dot"></span>
      <span class="brand-name">NORDVENT</span>
    </div>
    <span class="brand-tagline">AIR CONDITIONING &amp; REFRIGERATION</span>
  </div>

  <p class="issue-date">Issuing Date: May 5, 2018</p>
  <p class="recipient">Name Of Employee Mr. XYZABC<br>Address of Employee<br>Address Line 2 etc..</p>
  <p class="salutation">Dear Mr.XYZABC</p>

  <p class="paragraph p1">Lorem Ipsum has been the industry's standard dummy text ever since the 1500s, when an unknown printer took a galley of type and scrambled it to make a type specimen book. It has survived not only five centuries, but also the leap into electronic typesetting, remaining essentially unchanged. It was popularised in the 1960s with the release of Letraset sheets containing Lorem Ipsum passages, and more recently with desktop publishing software like Aldus PageMaker including versions of Lorem Ipsum.</p>
  <p class="paragraph p2">Lorem Ipsum is simply dummy text of the printing and typesetting industry. Lorem Ipsum has been the industry's standard dummy text ever since the 1500s, when an unknown printer took a galley of type and scrambled it to make a type specimen book.</p>
  <p class="paragraph p3">It has survived not only five centuries, but also the leap into electronic typesetting, remaining essentially unchanged. It was popularised in the 1960s with the release of Letraset sheets containing Lorem Ipsum passages.</p>

  <p class="closing">Yours Sincerely</p>
  <div class="signature-mark" role="img" aria-label="Handwritten signature of Daniel Archer"></div>
  <p class="signer-name">Daniel Archer</p>
  <p class="signer-title">Managing Director</p>

  <div class="footer-rule-red"></div>
  <div class="footer-rule-green"></div>
  <div class="footer-band"></div>

  <div class="contact">
    <div class="contact-line">021-555 010 203
      <svg viewBox="0 0 16 16"><path fill="#fff" d="M2 5c0-2 3-3 6-3s6 1 6 3v1h-3V5H5v1H2z M4 7h8l2 6H2z"/></svg>
    </div>
    <div class="contact-line">hello@nordvent.com
      <svg viewBox="0 0 16 16"><rect x="1" y="3" width="14" height="10" fill="#fff"/><path d="M1 3l7 6 7-6" fill="none" stroke="var(--charcoal)" stroke-width="1.3"/></svg>
    </div>
    <div class="contact-line">www.nordvent.com
      <svg viewBox="0 0 16 16"><circle cx="8" cy="8" r="7" fill="#fff"/><path d="M1 8h14M8 1c3 3 3 11 0 14M8 1c-3 3-3 11 0 14" fill="none" stroke="var(--charcoal)" stroke-width="1.2"/></svg>
    </div>
  </div>
  <p class="contact-address">18 Harbour Lane, Westfield, 30917</p>
</main>
</body>
</html>
```